Kestrel Facilities Business Card Design

We would now like to design business cards with the new Kestrel Facilities logo

Target Market(s)

Professional

Industry/Entity Type

Professional services

Contact Information for Business Card

Employee name, title, phone number, email address, corporate office address and logo.

Font styles to use
Sans Serif

Colors
0054AA
0677BA
7BADD7
CADEEF
E8F1F8

Requirements
Must have
• My logo
Should not have
• any other pictures or images besides my logo

```html
<!DOCTYPE html>
<html lang="en">
<head>
<meta charset="utf-8">
<title>Kestrel Facilities – Business Card</title>
<link href="https://fonts.googleapis.com/css2?family=Montserrat:wght@400;500;700&display=swap" rel="stylesheet">
<style>
  :root {
    --brand-blue: #2b7bc9;
    --ink: #3a3a3a;
    --card-white: #ffffff;
    --card-black: #1c1c1c;
    --backdrop: #e8f1f8;
  }
  * { margin: 0; padding: 0; box-sizing: border-box; }
  html, body {
    width: 1200px;
    height: 852px;
    overflow: hidden;
  }
  body {
    background: var(--backdrop);
    font-family: "Montserrat", sans-serif;
    display: flex;
    flex-direction: column;
    align-items: center;
    justify-content: center;
    gap: 40px;
  }
  .card {
    width: 640px;
    height: 366px;
    border-radius: 18px;
    position: relative;
    box-shadow: 0 10px 30px rgba(0, 0, 0, 0.18);
  }
  .card-back {
    background: var(--card-black);
    display: flex;
    align-items: center;
    justify-content: center;
  }
  .card-front {
    background: var(--card-white);
  }
  .brand {
    display: flex;
    align-items: center;
    gap: 14px;
    color: var(--brand-blue);
    font-weight: 700;
    letter-spacing: 0.02em;
    line-height: 1;
  }
  .brand-square {
    width: 40px;
    height: 40px;
    background: var(--brand-blue);
  }
  .card-back .brand { font-size: 34px; }
  .card-front .brand {
    position: absolute;
    top: 58px;
    right: 48px;
    font-size: 30px;
  }
  .holder {
    position: absolute;
    left: 48px;
    top: 150px;
  }
  .holder-name {
    color: var(--brand-blue);
    font-weight: 700;
    font-size: 24px;
  }
  .holder-title {
    color: var(--ink);
    font-weight: 400;
    font-size: 17px;
    margin-top: 2px;
  }
  .contact {
    position: absolute;
    left: 48px;
    bottom: 44px;
    font-size: 15px;
    color: var(--ink);
    line-height: 1.45;
  }
  .address { margin-bottom: 18px; }
  .contact-row { display: flex; }
  .contact-label {
    color: var(--brand-blue);
    font-weight: 700;
    width: 72px;
  }
  .contact-sep { width: 24px; }
</style>
</head>
<body>
  <section class="card card-back">
    <div class="brand">
      <span class="brand-square"></span>
      <span class="brand-name">Kestrel Facilities</span>
    </div>
  </section>

  <section class="card card-front">
    <div class="brand">
      <span class="brand-square"></span>
      <span class="brand-name">Kestrel Facilities</span>
    </div>

    <div class="holder">
      <p class="holder-name">Martin Hale</p>
      <p class="holder-title">Director</p>
    </div>

    <div class="contact">
      <p class="address">1187 Cedar Ridge Lane<br>Salem, OR 97301</p>
      <p class="contact-row"><span class="contact-label">Phone</span><span class="contact-sep">:</span><span>(503) 555-0142</span></p>
      <p class="contact-row"><span class="contact-label">Email</span><span class="contact-sep">:</span><span>info@kestrelfacilities.com</span></p>
    </div>
  </section>
</body>
</html>
```